Card Design for my dog training business Brightpaw Obedience

Need a business card design for my dog training business with my new logo. Want the card to come off professional yet fun. Want it to be very eye catchy as well. I normally have these at vet clinics, pet stores, and groomers. so need it to look better than my competitors.
Target Market(s)
dog owners
Industry/Entity Type
Dog Training
Contact Information for Business Card
needs logo, my name and info
Font styles to use
Serif
Colors
0255a3
ffffff
ec1f27
000000
333333
fbfbfb
Requirements
Must have
- Brightpaw Obedience
- Felix Orland
- 415 903 2276
- info@brightpawobedience.example
- www.brightpawobedience.example

```html
<!DOCTYPE html>
<html lang="en">
<head>
<meta charset="utf-8">
<title>Brightpaw Obedience – Business Card</title>
<link href="https://fonts.googleapis.com/css2?family=EB+Garamond:ital@1&family=Noto+Serif:wght@400&family=Open+Sans:wght@400&display=swap" rel="stylesheet">
<style>
  :root {
    --backdrop: #3b3b3d;
    --card: #1d1d1f;
    --silver: #c8c8c8;
    --muted: #9a9a9a;
    --contact: #bdbdbd;
    --accent-blue: #2a93d5;
    --accent-red: #ec1f27;
    --emblem-a: #4a4a4c;
    --emblem-b: #3a3a3c;
    --watermark-a: #2e3033;
    --watermark-b: #26282b;
  }
  * { margin: 0; padding: 0; box-sizing: border-box; }
  html, body {
    width: 799px; height: 1200px; overflow: hidden;
    background: var(--backdrop);
  }
  .sheet {
    width: 799px; height: 1200px;
    display: flex; flex-direction: column;
    justify-content: space-around; align-items: center;
    padding: 60px 0;
  }
  .card {
    position: relative;
    width: 580px; height: 330px;
    background: var(--card);
    border-radius: 4px;
    box-shadow: 0 18px 40px rgba(0,0,0,.45);
    overflow: hidden;
  }
  /* front */
  .card-front {
    display: flex; flex-direction: column;
    align-items: center; justify-content: center;
  }
  .front-emblem {
    width: 150px; height: 120px;
    border-radius: 6px;
    background: linear-gradient(135deg, var(--emblem-a), var(--emblem-b));
  }
  .brand {
    display: flex; align-items: center; gap: 8px;
    font-family: "Noto Serif", serif;
  }
  .brand-square {
    width: 10px; height: 10px; flex: none;
    background: var(--accent-red);
  }
  .front-brand {
    margin-top: 14px;
    font-size: 26px; color: var(--silver);
  }
  .front-tagline {
    margin-top: 16px;
    font-family: "EB Garamond", serif;
    font-style: italic; font-size: 16px;
    color: var(--muted);
  }
  /* back */
  .back-brand {
    position: absolute; left: 34px; top: 32px;
    font-size: 22px; color: var(--accent-blue);
  }
  .holder {
    position: absolute; left: 34px; top: 150px;
  }
  .holder-name {
    font-family: "Noto Serif", serif;
    font-size: 22px; color: var(--accent-blue);
  }
  .holder-role {
    font-family: "Open Sans", sans-serif;
    font-size: 12px; color: var(--muted);
    margin-top: 2px;
  }
  .contact-list {
    list-style: none;
    margin-top: 14px;
    display: flex; flex-direction: column; gap: 7px;
  }
  .contact-item {
    display: flex; align-items: center; gap: 10px;
    font-family: "Open Sans", sans-serif;
    font-size: 12.5px; color: var(--contact);
  }
  .contact-icon { width: 12px; height: 12px; flex: none; }
  .symbol-area {
    position: absolute; right: 0; bottom: 0;
    width: 260px; height: 260px;
    background: linear-gradient(135deg, var(--watermark-a), var(--watermark-b));
    border-top-left-radius: 40px;
  }
</style>
</head>
<body>
<main class="sheet">
  <section class="card card-front">
    <div class="front-emblem" role="img" aria-label="Brand emblem illustration"></div>
    <div class="brand front-brand"><span class="brand-square"></span>Brightpaw Obedience</div>
    <p class="front-tagline">“Training dogs across Texas one dog at a time.”</p>
  </section>

  <section class="card card-back">
    <div class="brand back-brand"><span class="brand-square"></span>Brightpaw Obedience</div>
    <div class="symbol-area" role="img" aria-label="Faint large brand emblem decoration"></div>
    <div class="holder">
      <div class="holder-name">Felix Orland</div>
      <div class="holder-role">Dog Trainer</div>
      <ul class="contact-list">
        <li class="contact-item">
          <svg class="contact-icon" viewBox="0 0 12 12"><path fill="#2a93d5" d="M2.5 1 4.5 1 5.3 3.6 4 4.6C4.6 6 5.9 7.3 7.4 8l1-1.3 2.6.8v2C11 10.5 10.5 11 9.5 11 5 11 1 7 1 2.5 1 1.5 1.5 1 2.5 1Z"/></svg>
          415 903 2276
        </li>
        <li class="contact-item">
          <svg class="contact-icon" viewBox="0 0 12 12"><rect x="1" y="2.5" width="10" height="7" fill="#2a93d5"/><path d="M1 2.5 6 6.5 11 2.5" fill="none" stroke="#1d1d1f" stroke-width="1"/></svg>
          info@brightpawobedience.example
        </li>
        <li class="contact-item">
          <svg class="contact-icon" viewBox="0 0 12 12"><circle cx="6" cy="6" r="5" fill="#2a93d5"/><path d="M1 6h10M6 1c-2 2.7-2 7.3 0 10M6 1c2 2.7 2 7.3 0 10" fill="none" stroke="#1d1d1f" stroke-width=".8"/></svg>
          www.brightpawobedience.example
        </li>
      </ul>
    </div>
  </section>
</main>
</body>
</html>
```